Webdesign für Gemeinschaftspraxis (13820)
Zielgruppe
Die Website ist für eine fachärztliche Gemeinschaftspraxis, die sich aus Internisten, Betriebsmedizinern, Präventionsärzten, Kardiologen, Allgemeinmedizinern und Phlebologen zusammensetzt.
Die Zielgruppe sind bestehende Patienten sowie potentielle Patienten.
Die Website soll informativ sein.
Aufgabenstellung
Die Website soll in schlichten Farben gehalten sein, die zum Logo und zu den Fotos passen.
Die Website soll als kurzer, informativer Auftritt dienen
Die gelieferten Fotos sollen verwendet werden.
Es soll eine Onepage-Website werden, die so aufgebaut ist, wie die Website unter dem folgenden Link: https://www.ihr-weg-zum-ziel-online.de/

```html
<!DOCTYPE html>
<html lang="de">
<head>
<meta charset="utf-8">
<title>Gemeinschaftspraxis Lindenhof</title>
<link rel="stylesheet" href="https://fonts.googleapis.com/css2?family=PT+Sans:wght@400;700&family=Fira+Sans:wght@400;600&display=swap">
<style>
:root{
  --navy-deep:#13224d;
  --navy:#1d2e62;
  --navy-team:#283c74;
  --blue-soft:#4c5f99;
  --blue-hours:#3e5390;
  --cell:#8593c2;
  --white:#ffffff;
  --ink:#1d2e62;
  --grey-text:#8a8f9c;
  --line:rgba(255,255,255,.28);
}
*{margin:0;padding:0;box-sizing:border-box}
html,body{width:1200px;height:4752px;overflow:hidden}
body{font-family:"Fira Sans",sans-serif;color:var(--white);background:var(--navy);position:relative}
section,header{position:absolute;left:0;width:1200px;overflow:hidden}
h2{font-family:"PT Sans",sans-serif;font-weight:400;letter-spacing:1px}

/* Navigation */
.site-nav{top:0;height:37px;background:var(--navy-deep);display:flex;justify-content:center;align-items:center;gap:26px;font-size:11px;letter-spacing:1px;z-index:3}
.site-nav a{color:rgba(255,255,255,.7);text-decoration:none}
.site-nav a.is-active{color:var(--white);font-weight:600}

/* Hero */
.hero{top:37px;height:768px}
.hero-photo{position:absolute;inset:0;background:linear-gradient(90deg,#c9c3b8 0%,#efeeea 30%,#f4f4f2 55%,#7a5a3e 80%,#5a4330 100%)}
.hero-circle{position:absolute;left:282px;top:24px;width:634px;height:634px;border-radius:50%;background:rgba(255,255,255,.95)}
.brand{position:absolute;left:0;width:100%;top:160px;text-align:center;font-family:"PT Sans",sans-serif;color:var(--ink)}
.brand-mark{display:inline-block;width:26px;height:26px;background:var(--ink);margin-bottom:10px}
.brand-name{font-size:22px;font-weight:700;letter-spacing:1px;text-transform:uppercase}
.brand-sub{font-size:12px;margin-top:4px}
.hero-title{position:absolute;left:399px;top:352px;font-size:41px;line-height:42px;color:var(--ink);font-family:"PT Sans",sans-serif}
.hero-text{position:absolute;left:401px;top:455px;width:410px;font-size:13px;line-height:20px;color:var(--grey-text)}

/* Big vertical words */
.vertical-word{position:absolute;font-family:"PT Sans",sans-serif;font-size:150px;color:rgba(255,255,255,.12);white-space:nowrap;transform:rotate(-90deg);transform-origin:center}

/* Leistungen */
.services{top:805px;height:1053px;background:var(--navy)}
.services h2{position:absolute;left:362px;top:92px;font-size:40px}
.service-list{position:absolute;left:365px;top:178px;width:507px;list-style:none}
.service-list li{height:36.9px;border-bottom:1px solid var(--line);display:flex;justify-content:space-between;align-items:center;font-size:13px}
.service-list svg{width:10px;height:10px}

/* Ärzte */
.doctors{top:1858px;height:798px;background:var(--blue-soft)}
.doctors h2{position:absolute;left:0;width:100%;text-align:center;top:92px;font-size:40px}
.doctor{position:absolute;top:194px;width:215px}
.doctor-photo{width:202px;height:202px;border-radius:50%;border:1px solid rgba(255,255,255,.45);background:rgba(255,255,255,.1);margin-left:0}
.doctor h3{font-size:17px;font-weight:600;margin-top:45px}
.doctor p{font-size:13px;line-height:21.5px;margin-top:20px}

/* Team */
.team{top:2656px;height:910px;background:var(--navy-team)}
.team h2{position:absolute;left:0;width:100%;text-align:center;top:92px;font-size:40px}
.team-photo{position:absolute;left:190px;top:197px;width:803px;height:407px;border:1px solid rgba(255,255,255,.35);background:rgba(255,255,255,.08)}
.team h3{position:absolute;left:201px;top:640px;font-size:17px;font-weight:600}
.team-text{position:absolute;top:689px;width:360px;font-size:13px;line-height:21px}

/* Öffnungszeiten */
.hours{top:3566px;height:1186px;background:var(--blue-hours)}
.hours h2{position:absolute;left:0;width:100%;text-align:center;top:94px;font-size:40px}
.hours-table{position:absolute;left:153px;top:180px;width:882px;border-collapse:collapse;font-size:13px}
.hours-table th{text-align:left;font-size:18px;font-weight:600;padding:0 5px 8px;border-bottom:1px solid var(--line)}
.hours-table td{vertical-align:top;padding:8px 5px 8px;border-bottom:1px solid var(--line)}
.hours-table td:first-child{font-weight:600;font-size:15px;width:132px}
.hours-table td:not(:first-child){width:150px}
.slot{display:block;width:111px;background:var(--cell);padding:5px 8px;line-height:20px}
.plain{display:block;padding:2px 8px}
.row-break td{color:rgba(255,255,255,.35);font-weight:400 !important;border-bottom:none}

/* Kontakt */
.contact-circle{position:absolute;left:282px;top:747px;width:634px;height:634px;border-radius:50%;background:#e8eaf2;color:var(--ink);text-align:center}
.contact-circle .brand{top:70px}
.address{position:absolute;top:205px;left:0;width:100%;font-size:13px;line-height:20px;color:var(--grey-text)}
.phone{position:absolute;top:297px;left:0;width:100%;font-size:13px;line-height:20px;color:var(--grey-text)}
.phone b{color:#6b7080}
</style>
</head>
<body>

<header class="site-nav">
  <a class="is-active">HOME</a><a>ÜBER UNS</a><a>LEISTUNGEN</a><a>ÄRZTE</a><a>TEAM</a><a>ÖFFNUNGSZEITEN</a><a>ADRESSE</a>
</header>

<section class="hero">
  <div class="hero-photo" role="img" aria-label="Foto des hellen Praxisflurs mit Empfangstresen und historischer Holztür"></div>
  <div class="hero-circle">
    <div class="brand" style="top:120px">
      <span class="brand-mark"></span>
      <div class="brand-name">Gemeinschaftspraxis Lindenhof</div>
      <div class="brand-sub">Dr. Brandt · Dr. Kessler · Wolters</div>
    </div>
  </div>
  <h1 class="hero-title">Kurzvorstellung der<br>Praxis dolor amet</h1>
  <p class="hero-text">Lorem ipsum dolor sit amet, consetetur sadipscing elitr, sed diam nonumy eirmod tempor invidunt ut labore et dolore magna aliquyam erat, sed diam voluptua. At vero eos et accusam et justo duo dolores et ea rebum. Stet clita kasd gubergren, no sea takimata sanctus est Lorem ipsum dolor sit amet.</p>
</section>

<section class="services">
  <div class="vertical-word" style="left:-175px;top:390px">Leistungen</div>
  <h2>Leistungen der Praxis</h2>
  <ul class="service-list">
    <li>Gesundheitsvorsorge/Prävention/ Gesundheits-Check-up<svg viewBox="0 0 10 10"><path d="M2 3.5l3 3 3-3" fill="none" stroke="#fff" stroke-width="1.4"/></svg></li>
    <li>Impfungen und Reiseimpfungen<svg viewBox="0 0 10 10"><path d="M2 3.5l3 3 3-3" fill="none" stroke="#fff" stroke-width="1.4"/></svg></li>
    <li>Impfungen und Reiseimpfungen<svg viewBox="0 0 10 10"><path d="M2 3.5l3 3 3-3" fill="none" stroke="#fff" stroke-width="1.4"/></svg></li>
    <li>Männervorsorge<svg viewBox="0 0 10 10"><path d="M2 3.5l3 3 3-3" fill="none" stroke="#fff" stroke-width="1.4"/></svg></li>
    <li>Diabetes mellitus<svg viewBox="0 0 10 10"><path d="M2 3.5l3 3 3-3" fill="none" stroke="#fff" stroke-width="1.4"/></svg></li>
    <li>Psychosomatische Grundversorgung<svg viewBox="0 0 10 10"><path d="M2 3.5l3 3 3-3" fill="none" stroke="#fff" stroke-width="1.4"/></svg></li>
    <li>Koronare Herzerkrankung (KHK)<svg viewBox="0 0 10 10"><path d="M2 3.5l3 3 3-3" fill="none" stroke="#fff" stroke-width="1.4"/></svg></li>
    <li>Asthma Bronchiale<svg viewBox="0 0 10 10"><path d="M2 3.5l3 3 3-3" fill="none" stroke="#fff" stroke-width="1.4"/></svg></li>
    <li>Palliativversorgung<svg viewBox="0 0 10 10"><path d="M2 3.5l3 3 3-3" fill="none" stroke="#fff" stroke-width="1.4"/></svg></li>
    <li>Prävention<svg viewBox="0 0 10 10"><path d="M2 3.5l3 3 3-3" fill="none" stroke="#fff" stroke-width="1.4"/></svg></li>
    <li>Echokardiografie<svg viewBox="0 0 10 10"><path d="M2 3.5l3 3 3-3" fill="none" stroke="#fff" stroke-width="1.4"/></svg></li>
    <li>Sonographische Untersuchung der Schilddrüse<svg viewBox="0 0 10 10"><path d="M2 3.5l3 3 3-3" fill="none" stroke="#fff" stroke-width="1.4"/></svg></li>
    <li>„Check-up“-Laboruntersuchungen sowie PSA-Wert und andere Tumormarker<svg viewBox="0 0 10 10"><path d="M2 3.5l3 3 3-3" fill="none" stroke="#fff" stroke-width="1.4"/></svg></li>
    <li>EKG und Belastungs-EKG<svg viewBox="0 0 10 10"><path d="M2 3.5l3 3 3-3" fill="none" stroke="#fff" stroke-width="1.4"/></svg></li>
    <li>Langzeit-Blutdruckmessung<svg viewBox="0 0 10 10"><path d="M2 3.5l3 3 3-3" fill="none" stroke="#fff" stroke-width="1.4"/></svg></li>
    <li>Lungenfunktionstest<svg viewBox="0 0 10 10"><path d="M2 3.5l3 3 3-3" fill="none" stroke="#fff" stroke-width="1.4"/></svg></li>
    <li>Disease-Management-Programme (DMP)<svg viewBox="0 0 10 10"><path d="M2 3.5l3 3 3-3" fill="none" stroke="#fff" stroke-width="1.4"/></svg></li>
    <li>Ultraschall der Bauchorgane<svg viewBox="0 0 10 10"><path d="M2 3.5l3 3 3-3" fill="none" stroke="#fff" stroke-width="1.4"/></svg></li>
    <li>Ultraschall der Hirnversorgenden Arterien (Duplexsonografie)<svg viewBox="0 0 10 10"><path d="M2 3.5l3 3 3-3" fill="none" stroke="#fff" stroke-width="1.4"/></svg></li>
    <li>Spiroergometrie<svg viewBox="0 0 10 10"><path d="M2 3.5l3 3 3-3" fill="none" stroke="#fff" stroke-width="1.4"/></svg></li>
  </ul>
</section>

<section class="doctors">
  <div class="vertical-word" style="left:945px;top:230px">Ärzte</div>
  <h2>Unsere Ärzte</h2>
  <article class="doctor" style="left:190px">
    <div class="doctor-photo" role="img" aria-label="Porträtfoto Dr. Brandt"></div>
    <h3>Dr. Vorname Brandt</h3>
    <p>Lorem ipsum dolor sit amet, conset etur sadipscing elitr, sed diam nonumy eirmod tempor invidunt ut labore et dolore magna aliquyam erat, sed diam voluptua. At vero eos et accusam et justo duo dolores et ea rebum. Stet clita kasd gubergren, no sea takimata sanctus est Lorem ipsum dolor sit amet.</p>
  </article>
  <article class="doctor" style="left:490px">
    <div class="doctor-photo" role="img" aria-label="Porträtfoto Dr. Kessler"></div>
    <h3>Dr. Vorname Kessler</h3>
    <p>Lorem ipsum dolor sit amet, conset etur sadipscing elitr, sed diam nonumy eirmod tempor invidunt ut labore et dolore magna aliquyam erat, sed diam voluptua. At vero eos et accusam et justo duo dolores et ea rebum. Stet clita kasd gubergren, no sea takimata sanctus est Lorem ipsum dolor sit amet.</p>
  </article>
  <article class="doctor" style="left:791px">
    <div class="doctor-photo" role="img" aria-label="Porträtfoto Wolters"></div>
    <h3>Vorname Wolters</h3>
    <p>Lorem ipsum dolor sit amet, conset etur sadipscing elitr, sed diam nonumy eirmod tempor invidunt ut labore et dolore magna aliquyam erat, sed diam voluptua. At vero eos et accusam et justo duo dolores et ea rebum. Stet clita kasd gubergren, no sea takimata sanctus est Lorem ipsum dolor sit amet.</p>
  </article>
</section>

<section class="team">
  <div class="vertical-word" style="left:-55px;top:235px">Team</div>
  <h2>Unser Team</h2>
  <div class="team-photo" role="img" aria-label="Gruppenfoto des Praxisteams"></div>
  <h3>Überschrift das Team</h3>
  <p class="team-text" style="left:201px">Lorem ipsum dolor sit amet, consetetur sadipscing elitr, sed diam nonumy eirmod tempor invidunt ut labore et dolore magna aliquyam erat, sed diam voluptua. At vero eos et accusam et justo duo dolores et ea rebum. Stet clita kasd gubergren, no sea takimata sanctus est Lorem ipsum.</p>
  <p class="team-text" style="left:608px">Lorem ipsum dolor sit amet, consetetur sadipscing elitr, sed diam nonumy eirmod tempor invidunt ut labore et dolore magna aliquyam erat, sed diam voluptua. At vero eos et accusam et justo duo dolores et ea rebum. Stet clita kasd gubergren, no sea takimata sanctus est.</p>
</section>

<section class="hours">
  <div class="vertical-word" style="left:900px;top:300px">Kontakt</div>
  <h2>Öffnungszeiten</h2>
  <table class="hours-table">
    <thead><tr><th>Zeit</th><th>Montag</th><th>Dienstag</th><th>Mittwoch</th><th>Donnerstag</th><th>Freitag</th></tr></thead>
    <tbody>
      <tr><td>Ab 7:30</td><td><span class="slot">Blutentnahme/ Ultraschall</span></td><td><span class="slot">Blutentnahme/ Ultraschall</span></td><td><span class="slot">Blutentnahme/ Ultraschall</span></td><td><span class="slot">Blutentnahme/ Ultraschall</span></td><td><span class="slot">Blutentnahme/ Ultraschall</span></td></tr>
      <tr><td>8:00-12:00</td><td><span class="slot">Freie Sprechstunde</span></td><td><span class="slot">Freie Sprechstunde</span></td><td><span class="slot">Freie Sprechstunde</span></td><td><span class="slot">Freie Sprechstunde</span></td><td><span class="slot">Freie Sprechstunde</span></td></tr>
      <tr><td>12:00 - 13:00</td><td><span class="plain">Hausbesuche</span></td><td><span class="plain">Hausbesuche</span></td><td><span class="plain">Hausbesuche</span></td><td><span class="plain">Hausbesuche</span></td><td><span class="plain">Hausbesuche</span></td></tr>
      <tr class="row-break"><td>13:00 - 15:30</td><td><span class="plain">Mittagspause</span></td><td><span class="plain">Mittagspause</span></td><td><span class="plain">Mittagspause</span></td><td><span class="plain">Mittagspause</span></td><td><span class="plain">Mittagspause</span></td></tr>
      <tr><td>15:30 - 16:00</td><td><span class="slot">Termin-sprechstunde</span></td><td><span class="slot">Termin-sprechstunde</span></td><td><span class="slot">Termin-sprechstunde</span></td><td><span class="slot">Termin-sprechstunde</span></td><td><span class="slot">Termin-sprechstunde</span></td></tr>
      <tr><td>16:00 - 18:00</td><td><span class="slot">Freie Sprechstunde</span></td><td><span class="slot">Freie Sprechstunde</span></td><td></td><td><span class="slot">Freie Sprechstunde</span></td><td></td></tr>
    </tbody>
  </table>

  <div class="contact-circle">
    <div class="brand">
      <span class="brand-mark"></span>
      <div class="brand-name" style="font-size:18px">Gemeinschaftspraxis Lindenhof</div>
      <div class="brand-sub" style="font-size:11px">Dr. Brandt · Dr. Kessler · Wolters</div>
    </div>
    <p class="address">Ahornweg 12<br>48155 Lindenhof<br>Nordrhein-Westfalen</p>
    <p class="phone"><b>Festnetztelefon:</b> 04521/334100<br><b>Fax:</b> 04521/334140</p>
  </div>
</section>

</body>
</html>
```